Halvery Construction Group Website

Need a dynamic corporate website that can be built on with time. We want to get our information out to the world and have a place where customers can submit requests for proposals.

Target Market(s)

Custom home owners and buyers. Architects and Real Estate Agents.

Industry/Entity Type

Construction

Number of Pages Required

3 page

Font styles to use
Serif
Sans Serif

Requirements
Must have
• Company logo, about, company contact information, biography, contact, projects,
• Sleek, modern, clean, attractive design.
• Online form customers can use for filling out a request for project proposal.
• Linkedin hyperlink.
• Uses www.halveryconstructiongroup.example

```html
<!DOCTYPE html>
<html lang="en">
<head>
<meta charset="utf-8">
<title>Halvery Construction Group</title>
<link href="https://fonts.googleapis.com/css2?family=Questrial&family=Open+Sans:ital,wght@0,400;0,600;0,700;1,400;1,600&display=swap" rel="stylesheet">
<style>
:root{
  --blue:#0e5da6;
  --blue-dark:#0a4d8c;
  --text:#555555;
  --grey-btn:#5a5a5a;
  --pale:#f3f7fa;
  --footer:#232222;
  --footer-bottom:#1b1b1b;
  --white:#ffffff;
  --muted:#9a9a9a;
}
*{margin:0;padding:0;box-sizing:border-box}
html,body{width:910px;height:1200px;overflow:hidden;background:var(--white)}
body{position:relative;font-family:"Open Sans",Arial,sans-serif;color:var(--text)}
.heading{font-family:"Questrial",Arial,sans-serif;font-weight:400}

.hero{position:absolute;left:0;top:0;width:910px;height:445px;border-top:2px solid var(--blue);
  background:
    radial-gradient(ellipse 380px 120px at 300px 150px,rgba(214,150,86,.55),rgba(214,150,86,0) 70%),
    radial-gradient(ellipse 260px 90px at 560px 200px,rgba(190,140,90,.4),rgba(190,140,90,0) 70%),
    linear-gradient(180deg,rgba(20,28,38,0) 55%,rgba(28,32,40,.85) 80%,#2a2c31 100%),
    linear-gradient(90deg,rgba(40,36,34,.5) 0%,rgba(40,36,34,0) 30%,rgba(30,40,55,0) 70%,rgba(25,35,50,.5) 100%),
    linear-gradient(180deg,#1a2533 0%,#3a4656 30%,#6e6a66 52%,#4c5058 70%,#2a2d33 100%)}
.brand{position:absolute;display:flex;align-items:center;gap:9px;color:var(--white)}
.brand-mark{width:44px;height:43px;background:var(--white)}
.brand-name{font-family:"Questrial",sans-serif;font-size:30px;line-height:1;letter-spacing:.5px}
.brand-sub{font-family:"Questrial",sans-serif;font-size:8.5px;letter-spacing:.2px;margin-top:1px}
.nav{position:absolute;top:39px;left:456px;display:flex;gap:36px;
  font-family:"Questrial",sans-serif;font-size:10.5px;color:var(--white)}
.search{position:absolute;left:811px;top:35px;width:24px;height:24px;border-radius:50%;background:#111}
.hero-title{position:absolute;top:193px;left:0;width:910px;text-align:center;color:var(--white);
  font-family:"Open Sans",sans-serif;font-size:24px;font-weight:600;letter-spacing:.4px}
.hero-text{position:absolute;top:228px;left:265px;width:380px;text-align:center;color:var(--white);
  font-family:"Questrial",sans-serif;font-size:12.5px;line-height:21.5px}
.arrow-btn{position:absolute;top:291px;width:22px;height:19px;border:1px solid var(--white)}

.about-title{position:absolute;top:472px;left:0;width:910px;text-align:center;color:var(--blue);font-size:21px}
.about-text{position:absolute;left:94px;width:722px;text-align:center;font-size:8.3px;line-height:17.5px}
.btn{position:absolute;top:613px;height:35px;font-family:"Questrial",sans-serif;font-size:9.5px;
  color:var(--white);display:flex;align-items:center;justify-content:center}
.btn-primary{left:350px;width:102px;background:linear-gradient(180deg,#1467b3,var(--blue-dark))}
.btn-secondary{left:458px;width:102px;background:linear-gradient(180deg,#666,#4e4e4e)}

.projects-band{position:absolute;top:684px;left:0;width:910px;height:117px;background:var(--pale)}
.projects-title{position:absolute;top:32px;width:910px;text-align:center;color:var(--blue);font-size:21px}
.projects-text{position:absolute;top:64px;left:150px;width:610px;text-align:center;font-size:8.3px;line-height:18.5px}

.project{position:absolute;top:801px;width:455px;height:244px;color:var(--white);text-align:center}
.project-left{left:0;background:
    linear-gradient(100deg,rgba(255,255,255,0) 55%,rgba(120,170,220,.25) 70%,rgba(255,255,255,0) 85%),
    linear-gradient(180deg,#2b79c2 0%,#1f68b0 55%,#175a9c 100%)}
.project-right{left:455px;background:
    radial-gradient(ellipse 160px 120px at 230px 170px,rgba(150,140,130,.35),rgba(150,140,130,0) 70%),
    linear-gradient(180deg,#3e4652 0%,#5d6068 45%,#3a3a3d 75%,#26272a 100%)}
.project h3{font-family:"Questrial",sans-serif;font-weight:400;font-size:11.5px;margin-top:66px}
.project .date{font-style:italic;font-weight:600;font-size:8.5px;margin-top:6px}
.project p{font-size:8.2px;line-height:16px;width:275px;margin:6px auto 0}
.view-btn{display:inline-flex;align-items:center;justify-content:center;width:75px;height:29px;
  border:2px solid var(--white);font-family:"Questrial",sans-serif;font-size:9.5px;margin-top:8px}

.footer{position:absolute;top:1045px;left:0;width:910px;height:115px;background:var(--footer);border-top:2px solid var(--blue)}
.footer h4{position:absolute;top:30px;font-family:"Questrial",sans-serif;font-weight:400;font-size:11.5px;color:var(--white)}
.footer-col{position:absolute;top:57px;font-size:8.2px;line-height:15px;color:#cfcfcf}
.email-field{position:absolute;left:600px;top:55px;width:160px;height:30px;background:var(--white);
  font-size:8.5px;color:#999;padding:9px 10px}
.subscribe{position:absolute;left:767px;top:55px;width:68px;height:30px;background:var(--blue);
  color:var(--white);font-size:9px;font-weight:700;letter-spacing:.5px;display:flex;align-items:center;justify-content:center}
.footer-bottom{position:absolute;top:1160px;left:0;width:910px;height:40px;background:var(--footer-bottom);
  font-size:8.2px;color:var(--muted)}
.social{position:absolute;top:9px;width:21px;height:21px;border:1.5px solid var(--white);border-radius:50%;
  display:flex;align-items:center;justify-content:center}
.social::after{content:"";width:5px;height:5px;border-radius:50%;background:var(--white)}
</style>
</head>
<body>

<header class="hero" role="img" aria-label="City skyline under construction with tower cranes at sunset">
  <div class="brand" style="left:75px;top:24px">
    <div class="brand-mark"></div>
    <div><div class="brand-name">HALVERY</div><div class="brand-sub">CONSTRUCTION GROUP, INC.</div></div>
  </div>
  <nav class="nav"><span>HOME</span><span>ABOUT</span><span>BIO</span><span>PROJECTS</span><span>CONTACT US</span></nav>
  <div class="search">
    <svg width="24" height="24" viewBox="0 0 24 24"><circle cx="11.3" cy="11.3" r="2.6" fill="none" stroke="#fff" stroke-width="1.3"/><line x1="13.2" y1="13.2" x2="15.2" y2="15.2" stroke="#fff" stroke-width="1.4"/></svg>
  </div>
  <h1 class="hero-title">HALVERY CONSTRUCTION GROUP</h1>
  <p class="hero-text">Nemo enim ipsam voluptatem quia voluptas sit aspernatur aut odit aut fugit, sed quia consequuntur magni dolores...</p>
  <div class="arrow-btn" style="left:430px"><svg width="20" height="17" viewBox="0 0 20 17"><polyline points="11.5,5 8,8.5 11.5,12" fill="none" stroke="#fff" stroke-width="1.6"/></svg></div>
  <div class="arrow-btn" style="left:457px"><svg width="20" height="17" viewBox="0 0 20 17"><polyline points="8.5,5 12,8.5 8.5,12" fill="none" stroke="#fff" stroke-width="1.6"/></svg></div>
</header>

<h2 class="about-title heading">ABOUT TO HALVERY CONSTRUCTION GROUP</h2>
<p class="about-text" style="top:502px">Nemo enim ipsam voluptatem quia voluptas sit aspernatur aut odit aut fugit, sed quia consequuntur magni dolores eos qui ratione voluptatem sequi nesciunt. Neque porro quisquam est, qui dolorem ipsum quia dolor sit amet, consectetur, adipisci velit, sed quia non numquam eius modi tempora incidunt ut labore et dolore magnam aliquam quaerat voluptatem. minima veniam, quis nostrum exercitationem ullam corporis suscipit laboriosam, nisi ut aliquid...</p>
<p class="about-text" style="top:561px">Lemo enim ipsam voluptatem quia voluptas sit aspernatur aut odit aut fugit, sed quia consequuntur magni dolores eos qui ratione voluptatem sequi nesciunt. Neque porro quisquam qui dolorem rat voluptatem. minima veniam, quis nostrum exercitationem ullam corporis suscipit laboriosam, nisi ut aliquid...</p>
<div class="btn btn-primary">READ MORE INFO</div>
<div class="btn btn-secondary">GET START TODAY</div>

<section class="projects-band">
  <h2 class="projects-title heading">PROJECTS</h2>
  <p class="projects-text">Nemo enim ipsam voluptatem quia voluptas sit aspernatur aut odit aut fugit, sed quia consequuntur magni dolores eos qui ratione voluptatem sequi<br>sed quia non numquam eius modi tempora incidunt ut labore et dolore magnam aliquam quaerat voluptatem.</p>
</section>

<article class="project project-left" role="img" aria-label="Blue-tinted high-rise buildings and a crane">
  <h3>NEMO ENIM IPSAM VOLUPTATEM</h3>
  <div class="date">August 28, 2016</div>
  <p>Nemo enim ipsam voluptatem quia voluptas sit aspernatur aut odit aut fugit, sed quia consequuntur magni dolores...</p>
  <div class="view-btn">View More</div>
</article>
<article class="project project-right" role="img" aria-label="Pedestrian bridge leading toward city towers">
  <h3>NEMO ENIM IPSAM VOLUPTATEM</h3>
  <div class="date">August 28, 2016</div>
  <p>Nemo enim ipsam voluptatem quia voluptas sit aspernatur aut odit aut fugit, sed quia consequuntur magni dolores...</p>
  <div class="view-btn">View More</div>
</article>

<footer class="footer">
  <div class="brand" style="left:75px;top:28px">
    <div class="brand-mark"></div>
    <div><div class="brand-name">HALVERY</div><div class="brand-sub">CONSTRUCTION GROUP, INC.</div></div>
  </div>
  <h4 style="left:305px">CONTACT US</h4>
  <div class="footer-col" style="left:305px"># lorem ipsum Dummy<br>Text mcg lorem</div>
  <div class="footer-col" style="left:419px">(000)-555-0142<br>info@halveryconstructiongroup.example</div>
  <h4 style="left:600px">NEWSLETTER</h4>
  <div class="email-field">Email:</div>
  <div class="subscribe">SUBSCRIBE</div>
</footer>

<div class="footer-bottom">
  <span style="position:absolute;left:75px;top:14px">© 2016 . halveryconstructiongroup | Allrights Reserved.</span>
  <span style="position:absolute;left:667px;top:14px">Connect With Us :</span>
  <span class="social" style="left:743px"></span>
  <span class="social" style="left:766px"></span>
  <span class="social" style="left:789px"></span>
  <span class="social" style="left:813px"></span>
</div>

</body>
</html>
```